Social Media Templates for Fieldhouse Raffle Fund

We need a set of Square (1080 x 1080) social media posts.

My company works with sports clubs, helping them to raise money with a lottery.

I need a set of social media image that I can use to appeal to new Fieldhouse Raffle Fund to encourage them to start a lottery with us.

This landing page has worked very well for us https://fieldhouserafflefund.com/fieldhouse-raffle-fund/

THING THAT APPEAL TO CLUBS

No Setup Fees/Start for Free - (We don’t charge any registration fees, or setup fees so you can start raising money from the first draw.)

Start Straight Away - (A club can start raising money straight away.)

Sustainable Income - (The average player plays for 7 years)

Subscription Lottery - (once a player joins, they play until the choose to leave. A club doesn't have to sell tickets every draw to the same people)

All Administration Taken Care Of - (We do all the hard work, so they can focus on running their club.)

Unlimited Income - (There is no limit on the amount of money a club can raise: the more players, the more funds for the club.)

Fundraising reach - (Reach new fans)

50% of the sales is guaranteed profit

£25,000 jackpot - (a person could win £25,000 every week)

Price - (It costs just £1 per week to enter)

Help Your Club - (100% of the profit goes to the club who a player chooses to support)

You can see all the clubs we work with on www.fieldhouserafflefund.com

The images will also be used on Chatterwall. You can see some examples here https://www.chatterwall.com/FieldhouseRaffleFund/ (you may need a proxy to view this page as it is only viewable in the UK, so I have attached some screenshots)

You can find the Fieldhouse Raffle Fund Logo here https://www.logovault.com/winwellgroup/

Target Market(s)

People who are involved with amateur sports in United Kingdom

Industry/Entity Type

Gambling

Font styles to use
Sans Serif

Requirements
Must have
• My project must look great on social social media and encourage people to get in touch about starting a lottery with us.

Adobe Suite files must be provided

```html
<!DOCTYPE html>
<html lang="en">
<head>
<meta charset="utf-8">
<title>Fieldhouse Raffle Fund – Help Your Club</title>
<link rel="stylesheet" href="https://fonts.googleapis.com/css2?family=Montserrat:wght@500;600;700;800;900&display=swap">
<style>
  :root {
    --backdrop: #3d3d3d;
    --purple-light: #a45fcc;
    --purple-mid: #9047bd;
    --purple-deep: #6f2a9e;
    --purple-circle: #8b2fc4;
    --white: #ffffff;
    --brand-blue: #2b82c4;
    --field-green: #6f9a4a;
    --field-dark: #3f5a33;
    --stand-dark: #3a2a4a;
  }
  html, body {
    margin: 0;
    width: 1200px;
    height: 1178px;
    overflow: hidden;
    background: var(--backdrop);
  }
  .post {
    position: absolute;
    left: 125px;
    top: 114px;
    width: 950px;
    height: 950px;
  }
  .post svg { display: block; }
  .type { font-family: 'Montserrat', sans-serif; }
  .intro-line { font-size: 36px; font-weight: 500; fill: var(--white); letter-spacing: 1px; }
  .headline { font-size: 96px; font-weight: 900; fill: var(--white); }
  .stat-figure { font-size: 158px; font-weight: 800; fill: var(--white); }
  .stat-caption { font-size: 43px; font-weight: 600; fill: var(--white); }
  .cta-join { font-size: 44px; font-weight: 500; fill: var(--purple-mid); }
  .cta-url { font-size: 38px; font-weight: 500; fill: var(--white); }
  .jackpot-amount { font-size: 136px; font-weight: 800; fill: var(--white); }
  .jackpot-label { font-size: 62px; font-weight: 800; fill: var(--white); }
  .brand-name { font-size: 21px; font-weight: 700; fill: var(--white); }
</style>
</head>
<body>
<div class="post">
  <svg width="950" height="950" viewBox="0 0 950 950" xmlns="http://www.w3.org/2000/svg">
    <defs>
      <linearGradient id="photoTone" x1="0" y1="0" x2="0" y2="1">
        <stop offset="0" stop-color="var(--stand-dark)"/>
        <stop offset="0.42" stop-color="#4a3b52"/>
        <stop offset="0.55" stop-color="var(--field-green)"/>
        <stop offset="1" stop-color="var(--field-dark)"/>
      </linearGradient>
    </defs>

    <rect class="photo" x="0" y="0" width="950" height="950" fill="url(#photoTone)"
          role="img" aria-label="Photo of a smiling footballer in a purple training top giving peace signs on a pitch, teammates and scoreboard behind"/>

    <g class="top-band">
      <polygon points="0,0 950,0 950,40 0,215" fill="var(--purple-light)" opacity="0.96"/>
      <polygon points="0,0 380,0 0,70" fill="var(--purple-deep)" opacity="0.55"/>
      <polygon points="560,0 950,0 950,20" fill="var(--purple-mid)" opacity="0.6"/>
    </g>

    <g class="type">
      <text class="intro-line" transform="translate(37 117) rotate(-11)">100% OF THE PROFIT GOES</text>
      <text class="intro-line" transform="translate(21 157) rotate(-11)">TO THE CLUB WHO A PLAYER</text>
      <text class="intro-line" transform="translate(87 183) rotate(-11)">CHOOSES TO SUPPORT</text>
    </g>

    <g class="headline-band" transform="rotate(-10 44 286)">
      <rect x="-40" y="205" width="1060" height="100" fill="var(--purple-mid)" opacity="0.6"/>
      <text class="type headline" x="44" y="286" textLength="900" lengthAdjust="spacingAndGlyphs">HELP YOUR CLUB</text>
    </g>

    <g class="stat">
      <circle cx="688" cy="486" r="219" fill="var(--purple-circle)" opacity="0.62"/>
      <g class="type" text-anchor="middle">
        <text class="stat-figure" x="700" y="499">50%</text>
        <text class="stat-caption" x="700" y="555">OF THE SALES IS</text>
        <text class="stat-caption" x="700" y="605">GUARANTEED</text>
        <text class="stat-caption" x="700" y="653">PROFIT</text>
      </g>
    </g>

    <g class="bottom-band">
      <polygon points="500,804 950,770 950,830" fill="var(--white)"/>
      <polygon points="0,774 950,840 950,950 0,950" fill="var(--purple-mid)"/>
      <polygon points="0,774 300,795 0,860" fill="var(--purple-light)" opacity="0.8"/>
      <polygon points="0,950 440,950 0,880" fill="var(--purple-light)" opacity="0.6"/>
      <polygon points="620,950 950,870 950,950" fill="var(--purple-light)" opacity="0.5"/>
    </g>

    <g class="cta">
      <polygon points="75,711 738,758 707,802 94,761" fill="var(--purple-mid)"/>
      <polygon points="135,707 232,664 666,692 694,749" fill="var(--white)"/>
      <text class="type cta-join" transform="translate(447 718) rotate(5)" text-anchor="middle">JOIN OUR LOTTERY</text>
      <text class="type cta-url" transform="translate(400 775) rotate(5)" text-anchor="middle" textLength="570" lengthAdjust="spacingAndGlyphs">www.fieldhouserafflefund.com</text>
    </g>

    <g class="brand">
      <rect x="762" y="714" width="18" height="18" fill="var(--brand-blue)"/>
      <text class="type brand-name" x="788" y="731">FIELDHOUSE</text>
      <text class="type brand-name" x="788" y="758">RAFFLE FUND</text>
    </g>

    <g class="type">
      <text class="jackpot-amount" x="22" y="927" textLength="593" lengthAdjust="spacingAndGlyphs">£25,000</text>
      <text class="jackpot-label" x="622" y="927" textLength="310" lengthAdjust="spacingAndGlyphs">JACKPOT</text>
    </g>
  </svg>
</div>
</body>
</html>
```